TK Homes - Stone Dorf Design

Looking for a double sides design, 1 side for my realestate and the other for home building. ( TK Homes on 1 side, Stone Dorf card on the other Side
Side 1 - Marek Tove ~ Vox Realty logo and Company ( the Property quarter )
Marek Tove
Marek@Marektove.example
IG - Marek_Bzq_Realtor
FB - marekt
Cell - 5558130467
3847 61 St Nw

Side 2
Marek Tove
5558130467
IG - Stonedorf_Bzq
Stonedorfdev@mailbox.example

Target Market(s)

Home buyers/ sellers

Industry/Entity Type

Home builders - Realestate

Contact Information for Business Card

Above

Requirements
Must have
• Black OR White background - my information -

```html
<!DOCTYPE html>
<html lang="en">
<head>
<meta charset="utf-8">
<title>Business cards</title>
<link rel="stylesheet" href="https://fonts.googleapis.com/css2?family=Tinos:wght@400;700&display=swap">
<style>
  :root {
    --stage: #232323;
    --card: #1f1f23;
    --blue: #0a72bb;
    --yellow: #fdcd45;
    --white: #ffffff;
    --rule: #cfcfcf;
  }
  * { box-sizing: border-box; margin: 0; padding: 0; }
  html, body {
    width: 1200px; height: 780px; overflow: hidden;
    background: var(--stage);
    font-family: "Tinos", "Times New Roman", serif;
  }
  .stage {
    width: 1200px; height: 780px;
    display: flex; flex-direction: column;
    align-items: center; justify-content: center; gap: 28px;
  }
  .card {
    position: relative;
    width: 640px; height: 360px;
    background: var(--card);
    border-radius: 22px;
    overflow: hidden;
    box-shadow: 0 14px 30px rgba(0,0,0,.6);
  }
  .card-shapes { position: absolute; inset: 0; width: 100%; height: 100%; }
  .divider {
    position: absolute; left: 282px; top: 62px;
    width: 1.5px; height: 226px;
    background: linear-gradient(to bottom, transparent, var(--rule) 20%, var(--rule) 80%, transparent);
  }
  .brand {
    position: absolute; left: 50px; width: 220px; top: 0; bottom: 0;
    display: flex; align-items: center; justify-content: center; gap: 10px;
  }
  .brand-mark { width: 14px; height: 14px; background: var(--yellow); flex: none; }
  .brand-name {
    font-weight: 700; font-size: 34px; line-height: 1.05;
    color: var(--blue); letter-spacing: .5px; text-align: center;
  }
  .details { position: absolute; left: 318px; top: 70px; color: var(--white); }
  .name { font-weight: 700; font-size: 34px; line-height: 1; }
  .name .first { color: var(--blue); }
  .name .last { color: var(--yellow); }
  .role { font-weight: 700; font-size: 16px; margin: 4px 0 12px 14px; }
  .contact-list { list-style: none; margin-left: 26px; }
  .contact-list li {
    display: flex; align-items: center; gap: 8px;
    font-size: 15px; line-height: 21px; white-space: nowrap;
  }
  .icon { width: 13px; height: 13px; flex: none; }
  .dot { width: 11px; height: 11px; border-radius: 50%; background: var(--blue); flex: none; margin: 0 1px; }
  .address {
    position: absolute; left: 360px; bottom: 30px;
    color: var(--white); font-size: 16px;
  }
</style>
</head>
<body>
<main class="stage">

  <section class="card card-builder">
    <svg class="card-shapes" viewBox="0 0 640 360" aria-hidden="true">
      <path d="M0 0 H175 C95 50 30 140 20 245 L0 245 Z" fill="var(--blue)"/>
      <path d="M640 95 C628 215 560 300 470 360 H640 Z" fill="var(--yellow)"/>
    </svg>
    <div class="brand">
      <span class="brand-mark"></span>
      <span class="brand-name">Stone Dorf</span>
    </div>
    <div class="divider"></div>
    <div class="details">
      <p class="name"><span class="first">Marek</span> <span class="last">Tove</span></p>
      <p class="role">Director</p>
      <ul class="contact-list">
        <li><svg class="icon" viewBox="0 0 16 16"><path d="M3 1l3 3-2 2c1 2 3 4 5 5l2-2 3 3-2 3C7 15 1 9 1 3z" fill="var(--blue)"/></svg>5558130467</li>
        <li><span class="dot"></span>Stonedorf_Bzq</li>
        <li><svg class="icon" viewBox="0 0 16 16"><rect x="1" y="3" width="14" height="10" fill="var(--blue)"/><path d="M1 3l7 6 7-6" stroke="var(--card)" stroke-width="1.4" fill="none"/></svg>Stonedorfdev@mailbox.example</li>
      </ul>
    </div>
  </section>

  <section class="card card-realty">
    <svg class="card-shapes" viewBox="0 0 640 360" aria-hidden="true">
      <path d="M0 0 H175 C95 50 30 140 20 245 L0 245 Z" fill="var(--blue)"/>
      <path d="M640 95 C628 215 560 300 470 360 H640 Z" fill="var(--yellow)"/>
    </svg>
    <div class="brand">
      <span class="brand-name">Marek<br>Tove</span>
    </div>
    <div class="divider"></div>
    <div class="details">
      <p class="name"><span class="first">Marek</span> <span class="last">Tove</span></p>
      <p class="role">Director</p>
      <ul class="contact-list">
        <li><svg class="icon" viewBox="0 0 16 16"><path d="M3 1l3 3-2 2c1 2 3 4 5 5l2-2 3 3-2 3C7 15 1 9 1 3z" fill="var(--blue)"/></svg>5558130467</li>
        <li><span class="dot"></span>marekt</li>
        <li><span class="dot"></span>Marek_Bzq_Realtor</li>
        <li><svg class="icon" viewBox="0 0 16 16"><rect x="1" y="3" width="14" height="10" fill="var(--blue)"/><path d="M1 3l7 6 7-6" stroke="var(--card)" stroke-width="1.4" fill="none"/></svg>Marek@Marektove.example</li>
        <li><svg class="icon" viewBox="0 0 16 16"><g fill="none" stroke="var(--blue)" stroke-width="1.4"><circle cx="8" cy="8" r="6.5"/><ellipse cx="8" cy="8" rx="3" ry="6.5"/><path d="M1.5 8h13M2.5 5h11M2.5 11h11"/></g></svg>www.marektove.example</li>
      </ul>
    </div>
    <p class="address">3847 61 St Nw</p>
  </section>

</main>
</body>
</html>
```